Coastline Premier Retreats Business Card Design

Design a business card for Coastline Premier Retreats. Look at the website for colors and reference. Card should have logo, name, title, office number, mobile number, email, URL and a tagline like, "Luxury Hotel & Resort Email Marketing" (This might change).

https://www.coastlinepremierretreats.example

The rest I will leave up to your imagination.

Contact Information for Business Card

Logo, name, title, office number, mobile number, email, URL and a tagline like, "Luxury Hotel & Resort Email Marketing" (This might change).

```html
<!DOCTYPE html>
<html lang="en">
<head>
<meta charset="utf-8">
<title>Coastline Premier Retreats – Business Card</title>
<link href="https://fonts.googleapis.com/css2?family=Arimo:wght@400;700&display=swap" rel="stylesheet">
<style>
  :root {
    --orange: #f07522;
    --ink: #111111;
    --paper: #ffffff;
    --backdrop: #dedede;
    --text: #1a1a1a;
  }
  * { box-sizing: border-box; margin: 0; padding: 0; }
  html, body {
    width: 1200px; height: 998px; overflow: hidden;
    background: var(--backdrop);
    font-family: "Arimo", Arial, sans-serif;
  }
  .canvas { position: relative; width: 1200px; height: 998px; }
  .card {
    position: absolute; width: 700px; height: 400px; overflow: hidden;
    box-shadow: 0 6px 18px rgba(0,0,0,0.18);
  }
  .card-front { left: 70px; top: 60px; background: var(--orange); }
  .card-back { left: 430px; top: 540px; background: var(--paper); }

  .brand-front {
    position: absolute; left: 0; right: 0; top: 150px;
    text-align: center; color: var(--paper);
    font-weight: 700; letter-spacing: 3px; line-height: 1.1;
  }
  .brand-front .brand-main { font-size: 58px; display: block; }
  .brand-front .brand-sub { font-size: 24px; letter-spacing: 10px; display: block; margin-top: 6px; }

  .brand-back {
    position: absolute; left: 50px; top: 140px;
    display: flex; align-items: center; gap: 12px;
    color: var(--ink); font-weight: 700; letter-spacing: 1px; line-height: 1.05;
  }
  .brand-back .brand-square { width: 16px; height: 16px; background: var(--orange); flex: none; }
  .brand-back .brand-main { font-size: 30px; display: block; }
  .brand-back .brand-sub { font-size: 13px; letter-spacing: 5px; display: block; margin-top: 4px; }

  .divider {
    position: absolute; left: 330px; top: 36px; width: 2px; height: 200px;
    background: var(--orange);
  }
  .contact { position: absolute; left: 350px; top: 28px; color: var(--text); }
  .contact-name {
    color: var(--orange); font-weight: 700; font-size: 24px; letter-spacing: 1px;
    text-transform: uppercase; margin-bottom: 6px;
  }
  .contact-role { font-size: 16px; line-height: 1.3; }
  .contact-list { list-style: none; margin-top: 8px; font-size: 16px; line-height: 1.45; }
  .contact-list li { display: flex; align-items: center; gap: 8px; }
  .contact-list svg { width: 14px; height: 14px; flex: none; fill: var(--orange); }

  .wave { position: absolute; left: 0; bottom: 0; width: 700px; height: 400px; }
</style>
</head>
<body>
<main class="canvas">
  <section class="card card-front" aria-label="Card front">
    <div class="brand-front">
      <span class="brand-main">COASTLINE</span>
      <span class="brand-sub">PREMIER RETREATS</span>
    </div>
  </section>

  <section class="card card-back" aria-label="Card back">
    <svg class="wave" viewBox="0 0 700 400" preserveAspectRatio="none" aria-hidden="true">
      <path d="M0 352 C 200 342, 330 318, 440 296 S 620 266, 700 262 L700 400 L0 400 Z" fill="var(--orange)"/>
      <path d="M0 344 C 200 334, 330 310, 440 288 S 620 258, 700 254" fill="none" stroke="var(--ink)" stroke-width="6"/>
      <path d="M0 348 C 200 338, 330 314, 440 292 S 620 262, 700 258" fill="none" stroke="var(--paper)" stroke-width="3"/>
    </svg>

    <div class="brand-back">
      <span class="brand-square"></span>
      <div>
        <span class="brand-main">COASTLINE</span>
        <span class="brand-sub">PREMIER RETREATS</span>
      </div>
    </div>

    <div class="divider"></div>

    <div class="contact">
      <p class="contact-name">Daniel Harwood</p>
      <p class="contact-role">Co-Founder</p>
      <p class="contact-role">Luxury Hotel &amp; Resort<br>Email Marketing</p>
      <ul class="contact-list">
        <li><svg viewBox="0 0 16 16"><path d="M3 2h3l1 4-2 1a9 9 0 0 0 4 4l1-2 4 1v3a2 2 0 0 1-2 2A12 12 0 0 1 1 4a2 2 0 0 1 2-2z"/></svg>555-210-3846</li>
        <li><svg viewBox="0 0 16 16"><path d="M4 1h8a1 1 0 0 1 1 1v12a1 1 0 0 1-1 1H4a1 1 0 0 1-1-1V2a1 1 0 0 1 1-1zm1 2v9h6V3zm3 10a.8.8 0 1 0 0 .1z"/></svg>555-730-6129</li>
        <li><svg viewBox="0 0 16 16"><path d="M1 3h14v10H1zm1 1.5V12h12V4.5L8 9z"/></svg>info@coastlinepremierretreats.example</li>
        <li><svg viewBox="0 0 16 16"><circle cx="8" cy="8" r="7"/></svg>www.coastlinepremierretreats.example</li>
      </ul>
    </div>
  </section>
</main>
</body>
</html>
```